Design for a real estate wev portal

Contents and features of the site
---------------------------------
Website in 5 languages: French, Dutch, English, German, Spanish.
English name of the site: Harbor Nest Place
Main purpose of the site:
- allow people to rent their house/ appartment for flatsharing purposes.
- help people wanting to find a room in flatsharing
- help people to find additional roommates for their flatsharing
Key interaction sequence:
1. I create a "group" of people who have common interest/hobbies
2. People who have the same interests/hobbies join my group
3. I look for a house/appartment to host my group
Website structure will be the following:
- Home
- Groups
-- Look for a group
--- Join a group
-- Create a group
- Properties
-- Look for a house/appartement
-- Apply
- Sales conditions
- Contact
- My account
-- My profile
-- My groups OR my properties
Your mission
------------
The client has no graphical guidelines, simply a logo (see attached).
We need a (responsive compliant) design for the following pages (we expect PSD's from you. No HTML nor CSS):
1. homepage (see example and wireframe attached)
2. properties search result list (see wireframe attached)
3. "detailed" form for properties
4. groups search result list
5. "detailed" form for groups
6. my account page
FOR THE COMPETITION step we only expect from you the design of first 2 screens.
Based on that, we will select the designer who will win the project, and will have to design the 4 remaining screens.
Target Market(s)
B2C
Industry/Entity Type
Real Estate
Number of Pages Required
5+ page
Look and feel
Each slider illustrates characteristics of the customer's brand and the style your logo design should communicate.

```html
<!DOCTYPE html>
<html lang="en">
<head>
<meta charset="utf-8">
<title>Harbor Nest Place</title>
<link href="https://fonts.googleapis.com/css2?family=Raleway:wght@400;500;600;700&family=Open+Sans:wght@400;600&display=swap" rel="stylesheet">
<style>
:root{
  --green:#6abf45;
  --teal:#17a0b2;
  --ink:#333;
  --muted:#666;
  --line:#e3e3e3;
  --soft:#f3f5f7;
  --footer:#505050;
  --footer-dark:#444;
  --white:#fff;
}
*{margin:0;padding:0;box-sizing:border-box}
html,body{width:1200px;height:2400px;overflow:hidden;background:var(--white)}
body{position:relative;font-family:"Open Sans",Arial,sans-serif;color:var(--ink)}
.abs{position:absolute}
h1,h2,h3,.nav a,.btn,.tile-label,.card-head{font-family:"Raleway",Arial,sans-serif}

/* header */
.site-header{position:absolute;left:0;top:0;width:1200px;height:115px;background:var(--white)}
.lang{left:115px;top:26px;width:117px;height:32px;border:1px solid #ccc;border-radius:3px;font-size:12px;line-height:30px;padding-left:32px;color:#444}
.lang::before{content:"";position:absolute;left:10px;top:11px;width:14px;height:9px;background:#9aa6c4}
.lang::after{content:"";position:absolute;right:10px;top:12px;border:4px solid transparent;border-top-color:#666}
.nav a{position:absolute;top:77px;font-size:13px;color:#555;text-decoration:none;letter-spacing:.3px}
.top-links a{position:absolute;top:30px;font-size:12px;color:#666;text-decoration:none;font-family:"Raleway",Arial,sans-serif}
.top-links .sep{position:absolute;top:29px;width:1px;height:14px;background:#888}
.brand{left:500px;top:30px;width:220px;height:60px;display:flex;align-items:center;gap:8px}
.brand-dot{width:14px;height:14px;border-radius:50%;background:var(--green)}
.brand-name{font-family:"Raleway",Arial,sans-serif;font-weight:700;font-size:21px;color:#2f3b45;letter-spacing:.3px}

/* hero */
.hero{left:0;top:115px;width:1200px;height:458px;background:linear-gradient(180deg,#6fa6d6 0%,#a9cbe6 30%,#8a7766 55%,#6b7d4f 80%,#7fa850 100%)}
.hero-caption{left:731px;top:215px;width:383px;height:198px;background:rgba(60,60,60,.78);padding:24px 24px}
.hero-caption h1{font-size:22px;font-weight:600;color:var(--white);letter-spacing:.5px;margin-bottom:14px}
.hero-caption p{font-size:11.5px;line-height:25px;color:#eee}
.dot{position:absolute;top:166px;width:15px;height:15px;border:2px solid var(--white);border-radius:50%}
.dot.on{background:var(--green)}

/* choice cards */
.choices{left:0;top:573px;width:1200px;height:393px;background:var(--soft)}
.card{position:absolute;top:43px;width:506px;height:314px;background:var(--white);border:1px solid var(--line)}
.card-head{height:45px;line-height:45px;padding-left:23px;color:var(--white);font-size:14px;font-weight:600;letter-spacing:.3px}
.card.seek .card-head{background:var(--green)}
.card.rent .card-head{background:var(--teal)}
.tile{position:absolute;top:61px;width:234px;height:237px;background:#f5f5f5}
.tile-photo{width:234px;height:141px}
.tile-label{text-align:center;font-size:18px;line-height:27px;color:#777;padding:12px 30px 0}

/* spotlight */
.section-title{font-size:19px;font-weight:500;color:#333;letter-spacing:.3px}
.listing{position:absolute;width:496px;height:176px;border:1px solid var(--line);background:var(--white)}
.listing-photo{position:absolute;left:11px;top:10px;width:177px;height:155px}
.listing h3{position:absolute;left:220px;top:16px;font-size:15px;font-weight:500;letter-spacing:.3px}
.listing p{position:absolute;left:220px;top:52px;font-size:11.5px;line-height:28px;color:#444}
.facts{position:absolute;left:220px;top:52px;font-size:11.5px;line-height:28px;color:#444;border-collapse:collapse}
.facts td{padding:0}
.facts td:first-child{width:112px}
.facts td:nth-child(2){width:48px}
.btn{position:absolute;height:42px;border:1.5px solid var(--green);color:var(--green);font-size:13.5px;font-weight:500;text-align:center;line-height:39px;letter-spacing:.3px;background:var(--white)}

/* selling band */
.band{left:0;top:1531px;width:1200px;height:256px}
.band h2{position:absolute;top:68px;font-size:17px;font-weight:600;color:var(--white);letter-spacing:.3px}
.band p{position:absolute;top:110px;width:480px;font-size:11px;line-height:29px;color:var(--white)}

/* faq */
.faq-item{position:absolute;left:86px;width:1028px;font-size:11.5px;line-height:25px;color:#555}
.faq-item a{color:var(--green);text-decoration:underline}
.rule{position:absolute;left:86px;width:1028px;height:1px;background:var(--line)}

/* footer */
.footer{left:0;top:2245px;width:1200px;height:86px;background:var(--footer)}
.follow{position:absolute;left:115px;top:30px;font-family:"Raleway",Arial,sans-serif;font-size:18px;font-weight:500;color:var(--white);letter-spacing:.5px}
.social{position:absolute;top:24px;width:38px;height:38px;border:2px solid var(--white);border-radius:50%}
.foot-btn{position:absolute;top:21px;height:43px;border:1.5px solid var(--white);color:var(--white);font-family:"Raleway",Arial,sans-serif;font-size:14px;font-weight:500;line-height:40px;text-align:center}
.legal{left:0;top:2331px;width:1200px;height:69px;background:var(--footer-dark);text-align:center;line-height:58px;font-size:11.5px;color:#eee}
</style>
</head>
<body>

<header class="site-header">
  <div class="abs lang">English</div>
  <nav class="nav">
    <a style="left:115px">HOME</a>
    <a style="left:229px">ABOUT US</a>
    <a style="left:366px">SERVICES</a>
    <a style="left:728px">PRODUCTS</a>
    <a style="left:869px">FEATURED</a>
    <a style="left:1007px">CONTACT US</a>
  </nav>
  <div class="abs brand"><span class="brand-dot"></span><span class="brand-name">Harbor Nest Place</span></div>
  <div class="top-links">
    <a style="left:773px">&#9998; CREATE</a>
    <span class="sep" style="left:861px"></span>
    <a style="left:885px">&#128274;&#xFE0E; LOGIN</a>
    <span class="sep" style="left:963px"></span>
    <a style="left:990px">&#9679; MY ACCOUNT</a>
  </div>
</header>

<section class="abs hero" role="img" aria-label="Photo of a suburban family house with a stone front porch, lawn and garden">
  <div class="abs hero-caption">
    <h1>HARBOR NEST PLACE</h1>
    <p>Sed ut perspiciatis unde omnis iste natus error sit voluptatem accusantium doloremque laudantium, totam rem aperiam, beatae vitae dicta sunt explicabo.</p>
    <span class="dot" style="left:312px"></span>
    <span class="dot on" style="left:331px"></span>
    <span class="dot" style="left:350px"></span>
  </div>
</section>

<section class="abs choices">
  <div class="card seek" style="left:85px">
    <div class="card-head">SEARCHING FOR ACCOMMODATION</div>
    <div class="tile" style="left:11px">
      <div class="tile-photo" role="img" aria-label="Photo of a white house with a porch" style="background:linear-gradient(180deg,#3f86d8,#cfd8e2 55%,#5d8f3e)"></div>
      <div class="tile-label">I want to rent a room right now!</div>
    </div>
    <div class="tile" style="left:259px">
      <div class="tile-photo" role="img" aria-label="Photo of a two-storey family house" style="background:linear-gradient(180deg,#2f7fd6,#a7a193 55%,#6e8a4c)"></div>
      <div class="tile-label">I want to join a group</div>
    </div>
  </div>
  <div class="card rent" style="left:608px">
    <div class="card-head">I HAVE A HOUSE FOR RENT</div>
    <div class="tile" style="left:11px">
      <div class="tile-photo" role="img" aria-label="Photo of a house with a garage and lawn" style="background:linear-gradient(180deg,#7fb2e0,#8c6e58 55%,#6ea546)"></div>
      <div class="tile-label">I want to advertise</div>
    </div>
    <div class="tile" style="left:259px">
      <div class="tile-photo" role="img" aria-label="Photo of a modern white house" style="background:linear-gradient(180deg,#7aaedb,#d9d9d6 55%,#6f9c4c)"></div>
      <div class="tile-label">Why is flatsharing interesting for me ?</div>
    </div>
  </div>
</section>

<h2 class="abs section-title" style="left:86px;top:995px">UNDER THE SPOTLIGHT</h2>
<h2 class="abs section-title" style="left:618px;top:995px">UNDER THE SPOTLIGHT</h2>

<article class="listing" style="left:86px;top:1043px">
  <div class="listing-photo" role="img" aria-label="Photo of a large family house" style="background:linear-gradient(180deg,#4e8fd4,#b9a98c 55%,#5f8d3d)"></div>
  <h3>A NICE GROUP</h3>
  <p>Young workers, seeking for<br>Accomodation downtown<br>Average age: 35<br>Men and women welcome</p>
</article>
<article class="listing" style="left:86px;top:1237px">
  <div class="listing-photo" role="img" aria-label="Photo of a group of young housemates outdoors" style="background:linear-gradient(180deg,#6d8c7a,#c9a58c 50%,#7a8c5a)"></div>
  <h3>ANOTHER NICE GROUP</h3>
  <p>Young ladies, studying at University<br>seeking for accomodation close to<br>Lindenhall University.<br>Average age: 20 Y Only Women</p>
</article>

<article class="listing" style="left:618px;top:1043px">
  <div class="listing-photo" role="img" aria-label="Photo of a modern villa with a pool and palm trees" style="background:linear-gradient(180deg,#b8d3ea,#e6e2da 50%,#6fae4a)"></div>
  <h3>HOUSE</h3>
  <table class="facts"><tr><td>House</td><td>-</td><td>2</td></tr><tr><td>Town</td><td>-</td><td>0</td></tr><tr><td>Rent per month</td><td>-</td><td>$ 25.00</td></tr><tr><td>Availability</td><td>-</td><td>2</td></tr></table>
</article>
<article class="listing" style="left:618px;top:1237px">
  <div class="listing-photo" role="img" aria-label="Photo of a lit house at dusk" style="background:linear-gradient(180deg,#2d5f9e,#9a6a45 55%,#3f5a34)"></div>
  <h3>APPARTMENT</h3>
  <table class="facts"><tr><td>House</td><td>-</td><td>2</td></tr><tr><td>Town</td><td>-</td><td>0</td></tr><tr><td>Rent per month</td><td>-</td><td>$ 25.00</td></tr><tr><td>Availability</td><td>-</td><td>2</td></tr></table>
</article>

<a class="btn" style="left:86px;top:1435px;width:190px">SEE MORE GROUPS</a>
<a class="btn" style="left:618px;top:1435px;width:190px">SEE MORE HOUSES</a>

<section class="abs band">
  <svg class="abs" width="1200" height="256" style="left:0;top:0" aria-hidden="true">
    <rect width="1200" height="256" fill="var(--teal)"/>
    <polygon points="0,0 565,0 634,256 0,256" fill="var(--green)"/>
  </svg>
  <h2 style="left:86px">KEY SELLING POINTS FOR THE ROOMMATES</h2>
  <p style="left:86px">Consectetuer adipiscing elit, sed diam nonummy nibh euismod tincidunt ut laoreet dolore magna aliquam erat volutpat. Ut wisi enim ad minim veniam, quis nostrud exerci tation ullamcorper suscipit lobortis nisi ut aliquip ex ea commodo consequa</p>
  <h2 style="left:642px">KEY SELLING POINTS FOR THE OWNERS</h2>
  <p style="left:642px">Consectetuer adipiscing elit, sed diam nonummy nibh euismod tincidunt ut laoreet dolore magna aliquam erat volutpat. Ut wisi enim ad minim veniam, quis nostrud exerci tation ullamcorper suscipit lobortis nisi ut aliquip ex ea commodo consequa</p>
</section>

<h2 class="abs section-title" style="left:86px;top:1837px">EVERYTHING YOU NEED TO KNOW ABOUT FLATSHARING</h2>
<p class="faq-item" style="top:1889px">Consectetuer adipiscing elit, sed diam nonummy nibh euismod tincidunt ut laoreet dolore magna aliquam erat volutpat. Ut wisi enim ad minim veniam, quis nostrud exerci tation ullamcorper suscipit lobortis nisi ut aliquip ex ea commodo consequa...<a>Read More &raquo;</a></p>
<div class="rule" style="top:1962px"></div>
<p class="faq-item" style="top:1978px">Consectetuer adipiscing elit, sed diam nonummy nibh euismod tincidunt ut laoreet dolore magna aliquam erat volutpat. Ut wisi enim ad minim veniam, quis nostrud exerci tation ullamcorper suscipit lobortis nisi ut aliquip ex ea commodo consequa...<a>Read More &raquo;</a></p>
<div class="rule" style="top:2051px"></div>
<p class="faq-item" style="top:2066px">Consectetuer adipiscing elit, sed diam nonummy nibh euismod tincidunt ut laoreet dolore magna aliquam erat volutpat. Ut wisi enim ad minim veniam, quis nostrud exerci tation ullamcorper suscipit lobortis nisi ut aliquip ex ea commodo consequa...<a>Read More &raquo;</a></p>
<div class="rule" style="top:2139px"></div>
<a class="btn" style="left:86px;top:2160px;width:190px">ALL QUESTIONS</a>

<footer class="abs footer">
  <span class="follow">FOLLOW US :</span>
  <span class="social" style="left:248px" aria-label="Social network link"></span>
  <span class="social" style="left:291px" aria-label="Social network link"></span>
  <span class="social" style="left:334px" aria-label="Social network link"></span>
  <span class="social" style="left:377px" aria-label="Social network link"></span>
  <span class="social" style="left:420px" aria-label="Social network link"></span>
  <a class="foot-btn" style="left:514px;width:224px">PRE-DEFINED SEARCHES</a>
  <a class="foot-btn" style="left:766px;width:242px">TOOLS AND INFORMATIONS</a>
</footer>
<div class="abs legal">&copy; Copy Rights 2016 Harbor Nest Place.All rights reserved</div>

</body>
</html>
```